Business Card Design - ChoiceCraft

Looking for creative, modern design, two sided for ChoiceCraft that is consistent with color and feel of website www.choicecraftpro.net.
Updates

Back of card will be used to promote products or have a quote revolving around decisions, change, leadership, innovation, creativity. Back should also have space to promote website, but optional to use the icon. Front of the card will need to use the icon and have standard place for name, job title, phone and email. We are not looking to put a mailing address or fax. Also want space to place a few words/phrase explaining what we do...such as individual growth and organizational development or tools, training, information...in addition, want the facebook icon small on the front somewhere as we are also on facebook.

Vector file uploaded of icon.

Target Market(s)

Professional coaching for individual growth and organizational development

Industry/Entity Type

Business

Requirements
Must have
• Icon...see attached.

```html
<!DOCTYPE html>
<html lang="en">
<head>
<meta charset="utf-8">
<title>ChoiceCraft Business Card</title>
<link href="https://fonts.googleapis.com/css2?family=Arimo:wght@400;700&display=swap" rel="stylesheet">
<style>
  :root {
    --page-bg: #e4e5e7;
    --card-bg: #ffffff;
    --navy: #1d3f7a;
    --sky: #2a9ad6;
    --ink: #222222;
    --muted: #9a9a9a;
    --rule: #c8c8c8;
    --mark-fill: #4d9fd9;
    --mark-soft: #d9ecf8;
  }
  * { box-sizing: border-box; margin: 0; padding: 0; }
  html, body {
    width: 1200px; height: 396px; overflow: hidden;
    background: var(--page-bg);
    font-family: "Arimo", Arial, sans-serif;
    color: var(--ink);
  }
  .card {
    position: absolute; top: 42px;
    width: 524px; height: 300px;
    background: var(--card-bg);
    border: 1px solid #b9b9b9;
    overflow: hidden;
  }
  .card--front { left: 47px; }
  .card--back { left: 612px; }

  /* Front */
  .brand-mark {
    position: absolute; left: 66px; top: 32px;
    width: 106px; height: 106px; border-radius: 50%;
    background: var(--mark-fill);
  }
  .brand-name {
    position: absolute; left: 0; width: 238px; top: 186px;
    text-align: center; font-size: 22px; font-weight: 700;
    letter-spacing: 0.5px; color: var(--ink);
  }
  .divider {
    position: absolute; left: 255px; top: 50px;
    width: 1px; height: 166px; background: var(--rule);
  }
  .identity { position: absolute; left: 273px; top: 56px; }
  .identity__name { font-size: 19px; font-weight: 700; color: var(--navy); }
  .identity__title { font-size: 14px; font-weight: 400; color: var(--navy); }
  .contacts { list-style: none; margin-top: 11px; }
  .contacts li {
    display: flex; align-items: center; gap: 6px;
    font-size: 14px; line-height: 18px; color: var(--ink);
  }
  .contacts svg { width: 11px; height: 11px; flex: none; }
  .social-square { width: 10px; height: 10px; background: var(--navy); flex: none; border-radius: 1px; }
  .tagline {
    margin-top: 11px; font-size: 14.5px; line-height: 18px;
    color: var(--ink); width: 250px;
  }
  .swoosh { position: absolute; left: 0; bottom: 0; width: 524px; height: 110px; }

  /* Back */
  .quotes { list-style: none; position: absolute; left: 26px; top: 24px; }
  .quote { position: relative; padding-left: 46px; height: 52.5px; }
  .quote__dot {
    position: absolute; left: 0; top: 5px;
    width: 16px; height: 16px; border-radius: 50%;
    background: var(--mark-fill);
  }
  .quote__text { font-size: 14px; line-height: 18px; color: var(--ink); position: relative; }
  .quote__text::before {
    content: "\201C"; position: absolute; left: -18px; top: -4px;
    font-size: 30px; font-weight: 700; color: var(--muted); line-height: 30px;
  }
  .quote__text::after {
    content: "\201D"; font-size: 30px; font-weight: 700; color: var(--ink);
    line-height: 0; vertical-align: -14px; margin-left: 1px;
  }
  .quote__author { font-size: 14px; font-weight: 700; color: var(--sky); margin-top: 2px; }
</style>
</head>
<body>
  <section class="card card--front" aria-label="Card front">
    <div class="brand-mark"></div>
    <div class="brand-name">ChoiceCraft</div>
    <div class="divider"></div>
    <div class="identity">
      <p><span class="identity__name">Your Name,</span> <span class="identity__title">Title</span></p>
      <ul class="contacts">
        <li><svg viewBox="0 0 12 12"><path d="M3 1 L5 3.5 L4 5 Q5.5 7.5 7 8 L8.5 7 L11 9 L9.5 11 Q4 10 1 3 Z" fill="none" stroke="#222" stroke-width="1"/></svg>123-456-789</li>
        <li><svg viewBox="0 0 12 12"><rect x="1" y="3" width="10" height="7" fill="none" stroke="#222" stroke-width="1.2"/><path d="M1 3 L6 7 L11 3" fill="none" stroke="#222" stroke-width="1.2"/></svg>info@choicecraftpro.net</li>
        <li><svg viewBox="0 0 12 12"><circle cx="6" cy="6" r="5" fill="none" stroke="#222" stroke-width="1.1"/><ellipse cx="6" cy="6" rx="2.2" ry="5" fill="none" stroke="#222" stroke-width="0.9"/><path d="M1 6 H11" stroke="#222" stroke-width="0.9"/></svg>www.choicecraftpro.net</li>
        <li><span class="social-square"></span>/choicecraftpro</li>
      </ul>
      <p class="tagline">Supporting individual growth and&nbsp; organizational development.</p>
    </div>
    <svg class="swoosh" viewBox="0 0 524 110" preserveAspectRatio="none">
      <defs>
        <linearGradient id="swoosh-blue" x1="0" y1="0" x2="1" y2="0">
          <stop offset="0" stop-color="#7fcdf2"/>
          <stop offset="0.6" stop-color="#3aa6e4"/>
          <stop offset="0.8" stop-color="#2a62b8"/>
          <stop offset="1" stop-color="#1c2f86"/>
        </linearGradient>
      </defs>
      <path d="M0 0 Q180 55 420 84 L524 94 L524 110 L0 110 Z" fill="#0c0c0c"/>
      <path d="M0 34 Q200 82 400 84 Q470 84 524 58 L524 110 L0 110 Z" fill="url(#swoosh-blue)"/>
      <path d="M0 34 Q200 82 400 84" fill="none" stroke="#ffffff" stroke-width="3"/>
    </svg>
  </section>

  <section class="card card--back" aria-label="Card back">
    <ul class="quotes">
      <li class="quote"><span class="quote__dot"></span>
        <p class="quote__text">Try not to become a man of success, but rather a man of value.</p>
        <p class="quote__author">- Alden Marsh</p></li>
      <li class="quote"><span class="quote__dot"></span>
        <p class="quote__text">The only constant is change.</p>
        <p class="quote__author">- Theron Vale</p></li>
      <li class="quote"><span class="quote__dot"></span>
        <p class="quote__text">We are what we repeatedly do. Excellence is not an act, it is a habit.</p>
        <p class="quote__author">- Corin Adell</p></li>
      <li class="quote"><span class="quote__dot"></span>
        <p class="quote__text">Simplicity is the ultimate sophistication.</p>
        <p class="quote__author">- Lucan Brevi</p></li>
      <li class="quote"><span class="quote__dot"></span>
        <p class="quote__text">Life is not fair - get used to it.</p>
        <p class="quote__author">- Wes Garrow</p></li>
    </ul>
  </section>
</body>
</html>
```